business card deign

Logo needs the following on it.
1. attached logo
2. Tagline - "If It Chills The Cooler Or Lifts The Crowd...We Bring It!"
3. Name- Dalton Pikes, Founder and CPO
4. Address - 412 E. Carver Avenue, Ste 2207, Tampa, FL. 33917
5. Phone - 555.318.4726

```html
<!DOCTYPE html>
<html lang="en">
<head>
<meta charset="utf-8">
<title>Hopley — Business Card</title>
<link rel="stylesheet" href="https://fonts.googleapis.com/css2?family=Roboto:wght@300;400;500;700&display=swap">
<style>
  :root {
    --stage: #3b3b3b;
    --card-top: #ffffff;
    --card-bottom: #e9e9e9;
    --ink: #0d0d0d;
    --band: #050505;
    --tagline: #7b7272;
    --rule: #9a9a9a;
    --art-light: #2a2a2a;
    --art-dark: #080808;
  }
  * { box-sizing: border-box; margin: 0; padding: 0; }
  html, body { width: 1200px; height: 900px; overflow: hidden; }
  body {
    background: var(--stage);
    font-family: "Roboto", Arial, sans-serif;
    color: var(--ink);
    position: relative;
  }
  .card {
    position: absolute;
    left: 250px;
    width: 700px;
    height: 400px;
    background: linear-gradient(135deg, var(--card-top) 0%, var(--card-top) 45%, var(--card-bottom) 100%);
    overflow: hidden;
    box-shadow: 0 8px 24px rgba(0,0,0,.45);
  }
  .card--front { top: 35px; }
  .card--back { top: 465px; }
  .card__band {
    position: absolute;
    left: 0; right: 0; bottom: 0;
    height: 52px;
    background: var(--band);
  }
  .card__art {
    position: absolute;
    left: 0; top: 60px; bottom: 0;
    width: 200px;
    background: linear-gradient(160deg, var(--art-light), var(--art-dark));
    border-top-right-radius: 90px;
  }
  .wordmark {
    position: absolute;
    font-weight: 700;
    text-transform: uppercase;
    color: var(--ink);
    line-height: 1;
    white-space: nowrap;
  }
  .card--front .wordmark {
    left: 240px; top: 180px;
    font-size: 60px;
    letter-spacing: 0.55em;
  }
  .rule {
    position: absolute;
    height: 1px;
    background: var(--rule);
  }
  .card--front .rule { left: 230px; right: 30px; top: 262px; }
  .tagline {
    position: absolute;
    font-weight: 700;
    font-size: 18px;
    color: var(--tagline);
    white-space: nowrap;
  }
  .card--front .tagline { left: 232px; top: 273px; }

  .logo-lockup {
    position: absolute;
    right: 50px; top: 70px;
    display: flex;
    align-items: center;
    gap: 14px;
  }
  .logo-lockup__mark {
    width: 34px; height: 34px;
    background: var(--ink);
  }
  .logo-lockup .wordmark {
    position: static;
    font-size: 36px;
    letter-spacing: 0.45em;
  }
  .contact {
    position: absolute;
    left: 232px; top: 232px;
    font-size: 15px;
    line-height: 1.45;
    white-space: nowrap;
  }
  .contact__name { font-weight: 700; text-transform: uppercase; }
  .contact__label { font-weight: 700; }
  .contact__detail { font-weight: 300; }
  .card--back .rule { left: 230px; right: 30px; top: 280px; }
  .card--back .tagline { left: 232px; top: 290px; }
</style>
</head>
<body>

<section class="card card--front">
  <div class="card__art" role="img" aria-label="Large black animal silhouette illustration"></div>
  <div class="wordmark">Hopley</div>
  <div class="rule"></div>
  <p class="tagline">If It Chills The Cooler Or Lifts The Crowd...We Bring It!</p>
  <div class="card__band"></div>
</section>

<section class="card card--back">
  <div class="card__art" role="img" aria-label="Large black animal silhouette illustration"></div>
  <div class="logo-lockup">
    <span class="logo-lockup__mark"></span>
    <span class="wordmark">Hopley</span>
  </div>
  <div class="contact">
    <p><span class="contact__name">Dalton Pikes</span> <span class="contact__label">|</span> <span class="contact__detail">Founder and CPO</span></p>
    <p><span class="contact__label">P.</span> <span class="contact__detail">555.318.4726</span> <span class="contact__label">|</span> <span class="contact__detail">412 E. Carver Avenue, Ste 2207, Tampa, FL. 33917</span></p>
  </div>
  <div class="rule"></div>
  <p class="tagline">If It Chills The Cooler Or Lifts The Crowd...We Bring It!</p>
  <div class="card__band"></div>
</section>

</body>
</html>
```